Dusty Spur Outfitters Home Page

I need a logo and page design for my home page, maybe some background color suggestions to go with it. I want the logo to project "vintage" and "western wear" but not be your typical trite western saddle and gun type thing.
http://www.dustyspuroutfitters.example/store/cart.php
Not looking for page coding just logo and other design elements to lay in over the site's template to make it "pop"
Reason: Have to finalize the design.
Target Market(s)
My customers are 70/30 men to women.
Industry/Entity Type
Gun

```html
<!DOCTYPE html>
<html lang="en">
<head>
<meta charset="utf-8">
<title>Dusty Spur Outfitters – Header Options</title>
<link rel="stylesheet" href="https://fonts.googleapis.com/css2?family=Lato:wght@700;900&family=Dancing+Script:wght@700&display=swap">
<style>
  :root {
    --canvas: #cfbe9f;
    --canvas-weave: #c7b594;
    --cream: #e9dfc8;
    --tagline: #ddd1b6;
    --search-ink: #33302b;
    --rust-mid: #4e2823;
    --rust-edge: #2f1a16;
    --teal: #3e97a6;
    --charcoal: #2e2f30;
    --charcoal-edge: #232425;
    --umber-mid: #55402a;
    --umber-edge: #2f2419;
  }
  * { margin: 0; padding: 0; box-sizing: border-box; }
  html, body { width: 1200px; height: 1000px; overflow: hidden; }
  body {
    position: relative;
    background-color: var(--canvas);
    background-image:
      repeating-linear-gradient(45deg, transparent 0 2px, rgba(0,0,0,0.025) 2px 3px),
      repeating-linear-gradient(-45deg, transparent 0 2px, rgba(255,255,255,0.04) 2px 3px);
    font-family: "Lato", Arial, sans-serif;
  }
  .header-option {
    position: absolute;
    left: 0;
    width: 1200px;
    height: 166px;
    box-shadow: 0 3px 6px rgba(40, 28, 15, 0.35);
  }
  .header-option--rust { top: 147px;
    background: linear-gradient(to bottom, var(--rust-edge) 0, var(--rust-mid) 18%, var(--rust-mid) 78%, var(--rust-edge) 100%); }
  .header-option--teal { top: 417px; background: var(--teal); }
  .header-option--teal .header-option__band {
    position: absolute; left: 0; right: 0; top: 14px; bottom: 16px;
    background: linear-gradient(to bottom, var(--charcoal-edge), var(--charcoal) 30%, var(--charcoal) 75%, var(--charcoal-edge));
  }
  .header-option--umber { top: 687px;
    background: linear-gradient(to bottom, var(--umber-edge) 0, var(--umber-mid) 18%, var(--umber-mid) 78%, var(--umber-edge) 100%); }

  .brand {
    position: absolute;
    left: 58px; top: 0;
    width: 408px; height: 166px;
    display: flex; align-items: center; justify-content: center; gap: 12px;
  }
  .brand__dot {
    width: 14px; height: 14px; border-radius: 50%;
    background: var(--cream);
  }
  .brand__name {
    font-family: "Lato", Arial, sans-serif;
    font-weight: 900;
    font-size: 30px;
    letter-spacing: 1px;
    text-transform: uppercase;
    color: var(--cream);
    white-space: nowrap;
  }
  .tagline {
    position: absolute;
    left: 476px; top: 86px;
    font-family: "Dancing Script", cursive;
    font-weight: 700;
    font-size: 25px;
    color: var(--tagline);
    white-space: nowrap;
  }
  .search {
    position: absolute;
    left: 901px; top: 53px;
    display: flex; align-items: center;
  }
  .search__field {
    width: 173px; height: 29px;
    border-radius: 15px;
    background: var(--cream);
    color: var(--search-ink);
    font-weight: 700; font-size: 17px;
    line-height: 29px;
    padding-left: 17px;
  }
  .search__go {
    margin-left: 10px;
    color: var(--tagline);
    font-weight: 700; font-size: 18px;
  }
</style>
</head>
<body>
  <header class="header-option header-option--rust">
    <div class="brand"><span class="brand__dot"></span><span class="brand__name">Dusty Spur Outfitters</span></div>
    <p class="tagline">Brand-New Retro Styled Western Wear</p>
    <div class="search"><span class="search__field">Search...</span><span class="search__go">GO!</span></div>
  </header>

  <header class="header-option header-option--teal">
    <div class="header-option__band"></div>
    <div class="brand"><span class="brand__dot"></span><span class="brand__name">Dusty Spur Outfitters</span></div>
    <p class="tagline">Brand-New Retro Styled Western Wear</p>
    <div class="search"><span class="search__field">Search...</span><span class="search__go">GO!</span></div>
  </header>

  <header class="header-option header-option--umber">
    <div class="brand"><span class="brand__dot"></span><span class="brand__name">Dusty Spur Outfitters</span></div>
    <p class="tagline">Brand-New Retro Styled Western Wear</p>
    <div class="search"><span class="search__field">Search...</span><span class="search__go">GO!</span></div>
  </header>
</body>
</html>
```